Design a Website for an IT Support Company

We are an IT support company that provides commercial IT support and services to small and medium sized businesses. We are in need of a website to be developed for our business.
We would like to work with someone who is either familiar with the IT field, or has developed a website for an IT support company in the past.
Some examples of designs/layouts that we like:
https://www.veldaworks.example/
http://www.marsbyquill.example/
http://817kq.example/
http://www.olbenstructures.example/
http://www.bykq.example/
I have attached a word document that gives a menu system/page layout format that we would like for our website as well as branch office phone numbers. Our logo is also attached that you can use for your design purposes. We currently do not have copy produced for all of the pages outlined in the word document, but would get this done during the project with the selected designer.
We would like the website to be SEO friendly & fully responsive. We would prefer a Wordpress format, however, we are open to HTML formats as well.

```html
<!DOCTYPE html>
<html lang="en">
<head>
<meta charset="utf-8">
<title>Vantora IT – IT Support</title>
<link rel="stylesheet" href="https://fonts.googleapis.com/css2?family=Open+Sans:wght@400;600;700&family=Titillium+Web:wght@600;700&display=swap">
<style>
:root{
  --blue:#0b6fc0;
  --blue-dark:#095a9c;
  --ink:#222;
  --muted:#777;
  --line:#dcdcdc;
  --pale:#f1f2f4;
  --footer:#1d1d1d;
  --white:#fff;
}
*{margin:0;padding:0;box-sizing:border-box}
html,body{width:1200px;height:3087px;overflow:hidden}
body{position:relative;background:var(--white);font-family:'Open Sans',Arial,sans-serif;color:var(--ink)}
.abs{position:absolute}
.heading{font-family:'Titillium Web','Arial Narrow',sans-serif;font-weight:700;letter-spacing:1.5px;text-transform:uppercase}

/* header */
.topbar{left:0;top:0;width:1200px;height:4px;background:var(--blue)}
.site-header{left:0;top:4px;width:1200px;height:103px;background:var(--white)}
.brand{left:97px;top:24px;display:flex;align-items:center;gap:12px}
.brand-mark{width:40px;height:40px;border-radius:50%;background:var(--blue)}
.brand-name{font-family:'Open Sans',sans-serif;font-weight:700;font-size:30px;color:var(--ink)}
.call{left:958px;top:20px;display:flex;gap:10px;align-items:center}
.call-icon{width:36px;height:36px;border-radius:50%;border:2px solid var(--blue);display:flex;align-items:center;justify-content:center}
.call small{display:block;font-size:10px;color:var(--ink)}
.call strong{display:block;font-size:16px;color:var(--blue);font-weight:600}
.main-nav{right:99px;top:74px;display:flex;gap:28px;font-size:14px;font-weight:600;color:var(--ink);align-items:center}
.main-nav .active{color:var(--blue)}

/* hero */
.hero{left:0;top:107px;width:1200px;height:583px;background:linear-gradient(100deg,#d9dadb 0%,#eef0ef 30%,#c7ccd0 55%,#e9ebea 75%,#9fa6ac 100%)}
.hero-title{left:0;top:355px;width:1200px;text-align:center;font-family:'Titillium Web',sans-serif;font-weight:700;font-size:74px;color:var(--white);letter-spacing:3px;text-shadow:0 3px 6px rgba(0,0,0,.35)}
.slider-tab{left:530px;top:650px;width:140px;height:40px;background:var(--white);border-radius:70px 70px 0 0}
.slider-dots{left:565px;top:670px;display:flex;gap:12px}
.slider-dots span{width:16px;height:16px;border-radius:50%;background:var(--blue)}
.slider-dots span:first-child{background:#9aa0a6}

/* section headings */
.section-title{left:0;width:1200px;text-align:center;font-size:28px;color:var(--blue)}
.divider{left:530px;width:140px;height:14px}
.divider::before{content:"";position:absolute;left:0;top:7px;width:140px;height:1px;background:#bbb}
.divider::after{content:"";position:absolute;left:62px;top:0;width:14px;height:14px;border-radius:50%;background:var(--white);border:3px solid var(--blue)}
.section-intro{left:270px;width:660px;text-align:center;font-size:12px;line-height:24px;color:var(--muted)}

/* services */
.service-card{top:1020px;width:312px;height:221px;background:var(--white);border:1px solid var(--line);box-shadow:0 1px 4px rgba(0,0,0,.08);text-align:center;padding-top:52px}
.service-card.featured{background:var(--blue);border-color:var(--blue);color:var(--white)}
.service-card h3{font-size:16px;font-weight:600;letter-spacing:.5px;margin-bottom:10px}
.service-card p{font-size:12px;line-height:23px;color:var(--muted);padding:0 40px}
.service-card.featured p{color:#e3eef8}
.service-card a{display:block;margin-top:14px;font-size:13px;font-weight:700;color:var(--blue);text-decoration:none}
.service-card.featured a{color:var(--white)}
.service-icon{top:949px;width:110px;height:110px;border-radius:50%;background:var(--white);border:2px solid var(--blue);display:flex;align-items:center;justify-content:center}

/* why */
.why-photo{left:0;top:1338px;width:600px;height:387px;background:linear-gradient(120deg,#e4e6e8 0%,#b9bfc4 40%,#4a5560 70%,#d8dadc 100%)}
.why-panel{left:600px;top:1338px;width:600px;height:387px;background:var(--blue);color:var(--white)}
.why-panel h2{position:absolute;left:63px;top:76px;font-size:26px}
.why-panel p{position:absolute;left:63px;top:138px;width:460px;font-size:12.5px;line-height:25px}
.btn-outline{position:absolute;left:63px;top:255px;width:148px;height:45px;border:2px solid var(--white);border-radius:8px;font-size:13px;font-weight:700;display:flex;align-items:center;justify-content:center;gap:6px}
.why-badge{left:571px;top:1496px;width:58px;height:58px;border-radius:50%;background:var(--blue);border:4px solid var(--white)}

/* blog */
.post{top:1955px;width:482px;height:218px;border:1px solid var(--line);background:var(--white);box-shadow:0 1px 4px rgba(0,0,0,.08)}
.post-photo{position:absolute;left:4px;top:4px;width:202px;height:208px}
.post-body{position:absolute;left:227px;top:26px;width:240px}
.post-body h3{font-size:16px;font-weight:600;line-height:24px;margin-bottom:12px}
.post-meta{font-size:12px;color:var(--muted);margin-bottom:12px;display:flex;gap:18px}
.post-body p{font-size:12px;line-height:22px;color:var(--muted);margin-bottom:10px}
.post-body a{font-size:12px;font-weight:700;color:var(--blue);text-decoration:none}

/* partners */
.partners{left:0;top:2270px;width:1200px;height:366px;background:linear-gradient(135deg,#eeeff1,#f7f7f8 50%,#ececee)}
.partner{top:2459px;width:185px;height:109px;background:var(--white);border:1px solid var(--line);display:flex;align-items:center;justify-content:center}
.partner span{width:110px;height:44px;border-radius:6px;background:#cfd2d5}

/* footer */
.site-footer{left:0;top:2636px;width:1200px;height:451px;background:var(--footer);color:var(--white)}
.footer-brand{position:absolute;left:97px;top:60px;display:flex;align-items:center;gap:12px}
.footer-about{position:absolute;left:97px;top:186px;width:300px;font-size:12px;line-height:28px}
.footer-col-title{position:absolute;top:64px;font-size:15px;font-weight:600;letter-spacing:.5px}
.numbers{position:absolute;left:384px;top:116px;font-size:12.5px;line-height:28px;list-style:none}
.field{position:absolute;border:1px solid #9a9a9a;font-size:10px;color:#ddd;padding:10px 12px}
.submit{position:absolute;left:679px;top:301px;width:99px;height:35px;background:var(--blue);border-radius:3px;font-size:12px;font-weight:700;display:flex;align-items:center;justify-content:center}
.footer-rule{position:absolute;left:97px;top:373px;width:1004px;height:1px;background:#555}
.copyright{position:absolute;left:97px;top:404px;font-size:11px}
.social{position:absolute;left:909px;top:394px;display:flex;gap:18px}
.social span{width:37px;height:37px;border-radius:50%;border:2px solid var(--white)}
</style>
</head>
<body>

<div class="abs topbar"></div>
<header class="abs site-header">
  <div class="abs brand">
    <span class="brand-mark"></span>
    <span class="brand-name">Vantora IT</span>
  </div>
  <div class="abs call">
    <span class="call-icon">
      <svg width="16" height="16" viewBox="0 0 24 24"><path fill="#0b6fc0" d="M6.6 10.8a15 15 0 0 0 6.6 6.6l2.2-2.2c.3-.3.7-.4 1-.2 1.1.4 2.3.6 3.6.6.6 0 1 .4 1 1V20c0 .6-.4 1-1 1A17 17 0 0 1 3 4c0-.6.4-1 1-1h3.5c.6 0 1 .4 1 1 0 1.3.2 2.5.6 3.6.1.3 0 .7-.2 1z"/></svg>
    </span>
    <span><small>Call Now!</small><strong>123 456 7890</strong></span>
  </div>
  <nav class="abs main-nav">
    <span class="active">HOME</span>
    <span>SERVICES</span>
    <span>WHY VANTORA IT</span>
    <span>ABOUT US</span>
    <span>BLOG</span>
    <span>CONTACT US</span>
    <svg width="14" height="14" viewBox="0 0 24 24"><circle cx="10" cy="10" r="7" fill="none" stroke="#222" stroke-width="3"/><path d="M15 15l6 6" stroke="#222" stroke-width="3"/></svg>
  </nav>
</header>

<section class="abs hero" role="img" aria-label="Photo of three business people shaking hands across a meeting table"></section>
<h1 class="abs hero-title">VANTORA IT</h1>
<div class="abs slider-tab"></div>
<div class="abs slider-dots"><span></span><span></span><span></span></div>

<!-- services -->
<h2 class="abs heading section-title" style="top:776px">Our Services</h2>
<div class="abs divider" style="top:825px"></div>
<p class="abs section-intro" style="top:858px">Lorem Ipsum is simply dummy text of the printing and typesetting industry. Lorem Ipsum has been the industry's standard dummy text ever since the 1500s, when an unknown printer took a galley of type book.</p>

<article class="abs service-card" style="left:97px">
  <h3>DATA SERVICES</h3>
  <p>Lorem Ipsum is simply dummy text of the printing and typesetting industry. Lorem Ipsum has been the industry's standard</p>
  <a>VIEW ALL DATA SERVICES &#10148;</a>
</article>
<article class="abs service-card featured" style="left:445px">
  <h3>CLOUD SERVICES</h3>
  <p>Lorem Ipsum is simply dummy text of the printing and typesetting industry. Lorem Ipsum has been the industry's standard</p>
  <a>VIEW ALL CLOUD SERVICES &#10148;</a>
</article>
<article class="abs service-card" style="left:789px">
  <h3>VOICE SERVICES</h3>
  <p>Lorem Ipsum is simply dummy text of the printing and typesetting industry. Lorem Ipsum has been the industry's standard</p>
  <a>VIEW ALL VOICE SERVICES &#10148;</a>
</article>

<div class="abs service-icon" style="left:198px">
  <svg width="56" height="56" viewBox="0 0 56 56" fill="none" stroke="#0b6fc0" stroke-width="3">
    <ellipse cx="24" cy="12" rx="16" ry="6"/><path d="M8 12v28c0 3.3 7.2 6 16 6M40 12v12M8 26c0 3.3 7.2 6 16 6"/>
    <rect x="32" y="34" width="18" height="14" rx="2" fill="#0b6fc0"/><path d="M36 34v-4a5 5 0 0 1 10 0v4"/>
  </svg>
</div>
<div class="abs service-icon" style="left:545px">
  <svg width="60" height="56" viewBox="0 0 60 56" fill="none" stroke="#0b6fc0" stroke-width="3">
    <path d="M16 28h30a9 9 0 0 0 0-18 13 13 0 0 0-25-2A10 10 0 0 0 16 28z"/>
    <path d="M30 28v8M12 36h36M12 36v6M30 36v6M48 36v6"/>
    <rect x="5" y="42" width="14" height="10"/><rect x="23" y="42" width="14" height="10"/><rect x="41" y="42" width="14" height="10"/>
  </svg>
</div>
<div class="abs service-icon" style="left:890px">
  <svg width="56" height="56" viewBox="0 0 56 56">
    <circle cx="28" cy="22" r="10" fill="#0b6fc0"/>
    <path d="M12 54c0-10 7-16 16-16s16 6 16 16z" fill="#0b6fc0"/>
    <path d="M14 24a14 14 0 0 1 28 0" fill="none" stroke="#0b6fc0" stroke-width="3"/>
    <rect x="10" y="20" width="6" height="10" rx="2" fill="#0b6fc0"/><rect x="40" y="20" width="6" height="10" rx="2" fill="#0b6fc0"/>
  </svg>
</div>

<!-- why -->
<div class="abs why-photo" role="img" aria-label="Photo of colleagues discussing work at a desk with a computer"></div>
<section class="abs why-panel">
  <h2 class="heading">Why Vantora IT</h2>
  <p>There are many variations of passages of Lorem Ipsum available, but the majority have suffered alteration in some form, by injected humour, or randomised the words which don't look even slightly believable.</p>
  <span class="btn-outline">READ MORE &#10148;</span>
</section>
<div class="abs why-badge"></div>

<!-- blog -->
<h2 class="abs heading section-title" style="top:1812px">Latest Blog Post</h2>
<div class="abs divider" style="top:1861px"></div>
<p class="abs section-intro" style="top:1890px">Lorem Ipsum is simply dummy text of the printing typesetting industry.</p>

<article class="abs post" style="left:97px">
  <div class="post-photo" role="img" aria-label="Photo of technicians working at monitors in a support centre" style="background:linear-gradient(135deg,#1b2a44,#3c5a85 55%,#2a3850)"></div>
  <div class="post-body">
    <h3>LOREM IPSUM IS SIMPLY THE DUMMY TEXT PRINTING</h3>
    <div class="post-meta"><span>&#9635; Auguest 01,</span><span>&#9679; Jhon.</span></div>
    <p>Lorem Ipsum is simply dummy text of the printing and typesetting industry.</p>
    <a>READ MORE &#10148;</a>
  </div>
</article>
<article class="abs post" style="left:619px">
  <div class="post-photo" role="img" aria-label="Photo of hands joining puzzle pieces on a table" style="background:linear-gradient(135deg,#3a3f47,#8a8f94 50%,#4f7a4a 70%,#2f3339)"></div>
  <div class="post-body">
    <h3>LOREM IPSUM IS SIMPLY THE DUMMY TEXT PRINTING</h3>
    <div class="post-meta"><span>&#9635; Auguest 01,</span><span>&#9679; Jhon.</span></div>
    <p>Lorem Ipsum is simply dummy text of the printing and typesetting industry.</p>
    <a>READ MORE &#10148;</a>
  </div>
</article>

<!-- partners -->
<section class="abs partners"></section>
<h2 class="abs heading section-title" style="top:2330px">Our Partners</h2>
<div class="abs divider" style="top:2378px"></div>
<p class="abs section-intro" style="top:2400px">Lorem Ipsum is simply dummy text of the printing typesetting industry.</p>
<div class="abs partner" style="left:98px"><span></span></div>
<div class="abs partner" style="left:302px"><span></span></div>
<div class="abs partner" style="left:507px"><span></span></div>
<div class="abs partner" style="left:712px"><span></span></div>
<div class="abs partner" style="left:915px"><span></span></div>

<!-- footer -->
<footer class="abs site-footer">
  <div class="footer-brand">
    <span class="brand-mark" style="width:44px;height:44px"></span>
    <span class="brand-name" style="color:#fff;font-size:32px">Vantora IT</span>
  </div>
  <p class="footer-about">Lorem Ipsum is simply dummy text of the printing and typesetting industry. Lorem Ipsum has been the industry's standard dummy text ever since the 1500s, when an unknown printer</p>

  <h3 class="footer-col-title" style="left:481px">CONTACT NUMBERS</h3>
  <ul class="numbers" style="left:481px">
    <li>Main Number: &nbsp; 555-210-4410</li>
    <li>Houston: &nbsp; 555-318-2207</li>
    <li>San Antonio: &nbsp; 555-426-7715</li>
    <li>Austin: &nbsp; 555-534-9082</li>
    <li>Tulsa: &nbsp; 555-642-1156</li>
    <li>Oklahoma City: &nbsp; 555-750-3348</li>
  </ul>

  <h3 class="footer-col-title" style="left:776px">CONTACT FORM</h3>
  <div class="field" style="left:776px;top:122px;width:157px;height:39px">Your Name</div>
  <div class="field" style="left:946px;top:122px;width:155px;height:39px">Enter Your Email</div>
  <div class="field" style="left:776px;top:171px;width:325px;height:39px">Enter Your Phone. No</div>
  <div class="field" style="left:776px;top:219px;width:325px;height:59px">Message</div>
  <div class="submit">SUBMIT</div>

  <div class="footer-rule"></div>
  <p class="copyright">© Copyright 2017 Vantora IT. All Rights Reserved</p>
  <div class="social"><span></span><span></span><span></span><span></span></div>
</footer>

</body>
</html>
```